CalmPeak Nurses' Manifesto

Design a manifesto to inspire and motivate nurses to work at minimum standards of excellence in their nursing practice.

The manifesto will become a feature of our website, at conferences, workshops and retreats. It will also be featured on other marketing tools.

Primary Market:
Nurses and/or other healthcare professionals (specifically Doctors, Occupational Therapists, Psychologists and Social Workers).

However the manifesto is equally applicable to all nurses and healthcare professionals from new graduates to very experienced senior clinicians, administration officers,managers and healthcare executive personnel.

Mainly females and primarily 35 to 65 years old, which suggests people in this target age group have extensive experience, but have become jaded'.

The purpose of our business is to assist healthcare professionals, primarily nurses, to maintain their enthusiasm and excellence in service provision, for their benefit as well as the benefit of the clients.

I have attached:
File 1: Copy Samples and examples: which has the copy for the manifesto, examples that appeal to us and our 3 attempts.
File 2: Our colour Spec Sheet, HOWEVER the colours are not necessary limited to these colours. These colours are not in the logo that will be on the manifesto. The colours on the logo attached can/or also be used.
File 3: Prototype logo. The final logo will be available within 3 to 4 days.

Industry/Entity Type

Healthcare

Requirements
Must have
• Must use the copy as per the attached file.

It should be contemporary, eye catching and motivational.

Should not have
• MUST BE EASY TO READ. Each line MUST be clearly defined from each other.

```html
<!DOCTYPE html>
<html lang="en">
<head>
<meta charset="utf-8">
<title>CalmPeak Nurses Manifesto</title>
<link rel="stylesheet" href="https://fonts.googleapis.com/css2?family=Bebas+Neue&family=Oswald:wght@400;500;600&family=Special+Elite&family=Courgette&display=swap">
<style>
  :root {
    --magenta: #d81f6d;
    --purple: #7a2f8f;
    --lavender: #b7a2d4;
    --teal: #1ea4ab;
    --green: #8cc43f;
    --orange: #f6931f;
    --rule: #e3dbe9;
    --paper: #ffffff;
  }
  * { margin: 0; padding: 0; box-sizing: border-box; }
  html, body { width: 793px; height: 1200px; overflow: hidden; background: var(--paper); }
  .poster { position: relative; width: 793px; height: 1200px; background: var(--paper); overflow: hidden; }
  .block { position: absolute; white-space: nowrap; }
  .rule { position: absolute; left: 32px; width: 729px; height: 3px; }
  .vrule { position: absolute; width: 3px; }
  .bebas { font-family: "Bebas Neue", "Oswald", sans-serif; font-weight: 400; }
  .oswald { font-family: "Oswald", sans-serif; }
  .elite { font-family: "Special Elite", "Courier New", monospace; }
  .script { font-family: "Courgette", cursive; }

  .title { top: 22px; left: 32px; width: 729px; text-align: center; color: var(--magenta); font-size: 84px; letter-spacing: 9px; line-height: 1; }

  .open-hands { top: 118px; left: 32px; width: 340px; color: var(--lavender); font-size: 50px; line-height: 0.96; }
  .self-care { top: 120px; left: 394px; width: 367px; color: var(--purple); font-size: 17px; line-height: 1.25; font-weight: 500; }
  .self-care b { font-weight: 600; }
  .delight { top: 186px; left: 394px; width: 367px; color: var(--teal); font-size: 29px; line-height: 1; }

  .support { top: 280px; left: 32px; width: 350px; color: var(--green); font-size: 30px; line-height: 1.05; }
  .respect-word { top: 270px; left: 400px; width: 361px; color: var(--orange); font-size: 60px; letter-spacing: 10px; line-height: 1; }
  .respect-text { top: 326px; left: 400px; width: 361px; color: var(--orange); font-size: 14px; line-height: 1.2; }

  .learn { top: 376px; left: 32px; width: 729px; color: var(--teal); font-size: 54px; letter-spacing: 3.4px; line-height: 1; }
  .trust { top: 428px; left: 32px; width: 729px; color: var(--green); font-size: 21px; line-height: 1.2; }

  .lifelong { top: 478px; left: 32px; width: 340px; color: var(--orange); line-height: 0.9; }
  .lifelong .small { display: block; font-size: 50px; letter-spacing: 2px; }
  .lifelong .big { display: block; font-size: 80px; letter-spacing: 4px; }
  .diversity { top: 494px; left: 400px; width: 361px; color: var(--lavender); font-size: 30px; line-height: 1.05; }

  .smile { top: 608px; left: 32px; width: 729px; color: var(--green); font-size: 25px; line-height: 1.1; font-weight: 500; }

  .right-thing { top: 660px; left: 32px; width: 345px; color: var(--teal); font-size: 40px; line-height: 0.95; }
  .right-thing .mid { font-size: 50px; }
  .unique { top: 660px; left: 400px; width: 361px; color: var(--lavender); font-size: 44px; line-height: 0.98; }
  .within { top: 752px; left: 400px; width: 361px; color: var(--teal); font-size: 25px; line-height: 1; letter-spacing: 1px; }

  .solution { top: 800px; left: 32px; width: 729px; color: var(--orange); font-size: 40px; letter-spacing: 1px; line-height: 1; }

  .leaders { top: 868px; left: 32px; width: 440px; color: var(--magenta); font-size: 34px; line-height: 1; }
  .lead-purpose { top: 910px; left: 32px; width: 440px; color: var(--purple); font-size: 14px; font-weight: 500; letter-spacing: 0.3px; }
  .respond { top: 942px; left: 32px; width: 440px; color: var(--magenta); font-size: 18px; line-height: 1.25; }

  .lead-box { top: 866px; left: 496px; width: 265px; height: 168px; border: 3px solid var(--lavender); padding: 12px 14px; color: var(--green); white-space: nowrap; }
  .lead-box .line1 { display: block; font-size: 30px; line-height: 1; }
  .lead-box .line2 { display: block; font-size: 30px; line-height: 1.05; }
  .lead-box .shout { display: block; font-size: 76px; line-height: 0.95; letter-spacing: 3px; }

  .choose { top: 1046px; left: 32px; width: 440px; color: var(--teal); font-size: 20px; line-height: 1.2; font-weight: 500; }
  .choose .big { font-size: 26px; font-family: "Bebas Neue", sans-serif; font-weight: 400; letter-spacing: 1px; }
  .can-do { top: 1050px; left: 496px; width: 265px; color: var(--magenta); font-size: 15px; line-height: 1.3; font-weight: 500; }

  .dream { top: 1112px; left: 32px; width: 460px; color: var(--purple); font-size: 68px; letter-spacing: 3px; line-height: 1; }

  .brand { top: 1124px; left: 596px; width: 165px; display: flex; align-items: center; justify-content: flex-end; gap: 10px; color: var(--magenta); font-family: "Oswald", sans-serif; font-weight: 500; font-size: 22px; }
  .brand .dot { width: 22px; height: 22px; border-radius: 50%; background: var(--teal); }
</style>
</head>
<body>
<main class="poster">
  <div class="rule" style="top:14px;background:var(--magenta)"></div>
  <h1 class="block title bebas">Nurses Manifesto</h1>
  <div class="rule" style="top:106px;background:var(--rule)"></div>

  <p class="block open-hands bebas">Nurse with<br>open hands,<br>hearts &amp; minds</p>
  <div class="vrule" style="top:118px;left:380px;height:136px;background:var(--rule)"></div>
  <p class="block self-care oswald">Look after <b>YOURSELF &amp; VALUE YOUR HEALTH</b><br>as much as you value the <b>HEALTH OF OTHERS</b></p>
  <p class="block delight bebas">Delight your clients &amp; colleagues<br>by exceeding their expectations</p>

  <div class="rule" style="top:266px;background:var(--rule)"></div>
  <p class="block support bebas">Support your colleagues and<br>champion their purpose.</p>
  <div class="vrule" style="top:276px;left:388px;height:80px;background:var(--rule)"></div>
  <p class="block respect-word bebas">Respect</p>
  <p class="block respect-text oswald">the limits of people’s KNOWLEDGE &amp;<br>SHARE YOUR knowledge generously.</p>

  <div class="rule" style="top:366px;background:var(--rule)"></div>
  <p class="block learn bebas">Learn something new each day</p>
  <p class="block trust script">Trust your knowledge &amp; seek advice only from respected sources.</p>

  <div class="rule" style="top:468px;background:var(--rule)"></div>
  <p class="block lifelong bebas"><span class="small">Be a lifelong</span><span class="big">Learner</span></p>
  <div class="vrule" style="top:480px;left:388px;height:108px;background:var(--rule)"></div>
  <p class="block diversity bebas">Celebrate, respect and value the<br>diversity of Australian culture.</p>

  <div class="rule" style="top:598px;background:var(--rule)"></div>
  <p class="block smile oswald">SMILE &amp; INFECT others with your HAPPINESS &amp; have FUN!</p>
  <div class="rule" style="top:650px;background:var(--rule)"></div>

  <p class="block right-thing bebas">Always do<br><span class="mid">the right thing</span><br>with out exception</p>
  <div class="vrule" style="top:660px;left:388px;height:122px;background:var(--rule)"></div>
  <p class="block unique bebas">You are unique, revel<br>in your individuality.</p>
  <p class="block within bebas">Seek success firstly from within.</p>

  <div class="rule" style="top:790px;background:var(--rule)"></div>
  <p class="block solution elite">ALWAYS BE SOLUTION FOCUSED</p>
  <div class="rule" style="top:852px;background:var(--rule)"></div>

  <p class="block leaders bebas">Only follow exceptional leaders.</p>
  <p class="block lead-purpose oswald">ALWAYS LEAD WITH PURPOSE, PASSION &amp; COMMITMENT.</p>
  <p class="block respond elite">“RESPOND to complex situations<br>INNOVATIVELY, CREATIVELY &amp; SAFELY<br>within the scope of your practice.”</p>

  <div class="block lead-box bebas">
    <span class="line1">If there is no one</span>
    <span class="line2">left to follow, then</span>
    <span class="shout">Lead!</span>
  </div>

  <div class="rule" style="top:1036px;left:32px;width:450px;background:var(--rule)"></div>
  <p class="block choose oswald">CHOOSE your thoughts wisely, they create<br><span class="big">YOUR REALITY.</span></p>
  <p class="block can-do oswald">ADOPT A ‘CAN DO’ ATTITUDE to<br>EVERYTHING THAT COMES YOUR WAY.</p>

  <p class="block dream bebas">Live your dream</p>
  <div class="block brand"><span class="dot"></span><span>CalmPeak</span></div>
  <div class="rule" style="top:1186px;background:var(--magenta)"></div>
</main>
</body>
</html>
```